​Silver Harbor Rhythm provides personal, friendly service in a fun and high energy environment. We are based in Vermont.

We would like a card that appeals to a wide range of audiences as we do a wide range of events. Please feel free to check out our website silverharborrhythm.net for inspiration.

Target Market(s)

weddings, corporate, birthday parties, colleges

Industry/Entity Type

Business

Contact Information for Business Card

Silver Harbor Rhythm
Providing Entertainment For All Occasions
555 274 9160
silverharborrhythm@mailnest.net
silverharborrhythm.net

```html
<!DOCTYPE html>
<html lang="en">
<head>
<meta charset="utf-8">
<title>Silver Harbor Rhythm – Business Card</title>
<link rel="stylesheet" href="https://fonts.googleapis.com/css2?family=Open+Sans:wght@400;600;700&display=swap">
<style>
  :root {
    --canvas: #e9e7e3;
    --card: #ffffff;
    --green-dark: #2f5a1c;
    --green-band: #3b6b22;
    --green-line: #24461a;
    --ink: #3a3a3a;
    --on-green: #ffffff;
  }
  * { box-sizing: border-box; margin: 0; padding: 0; }
  html, body {
    width: 1200px; height: 1200px; overflow: hidden;
    background: var(--canvas);
    font-family: "Open Sans", Arial, sans-serif;
  }
  .canvas {
    width: 1200px; height: 1200px;
    display: flex; flex-direction: column; align-items: center; justify-content: center;
    gap: 70px;
  }
  .card {
    position: relative;
    width: 820px; height: 470px;
    background: var(--card);
    border-radius: 26px;
    overflow: hidden;
    box-shadow: 0 6px 18px rgba(0,0,0,.18);
  }
  /* front */
  .brand-name {
    font-weight: 700;
    color: var(--green-dark);
    letter-spacing: .02em;
    text-transform: uppercase;
    text-align: center;
  }
  .card--front .brand-name {
    position: absolute; top: 92px; left: 0; right: 0;
    font-size: 40px;
  }
  .card--front .brand-mark {
    position: absolute; top: 40px; left: 50%;
    width: 34px; height: 34px; margin-left: -17px;
    border-radius: 50%; background: var(--green-dark);
  }
  .person {
    position: absolute; top: 178px; left: 0; right: 0;
    text-align: center;
    font-weight: 700; font-size: 26px; color: var(--green-dark);
  }
  .band { position: absolute; left: 0; top: 0; width: 820px; height: 470px; }
  .contact {
    position: absolute; left: 0; right: 0; bottom: 22px;
    color: var(--on-green); font-size: 17px;
  }
  .contact-row { display: flex; justify-content: center; align-items: center; gap: 8px; margin-top: 12px; }
  .contact-row svg { width: 16px; height: 16px; flex: none; }
  .contact-row .spacer { width: 14px; }
  .contact-row--left { justify-content: flex-start; padding-left: 48px; }
  /* back */
  .card--back .brand-name {
    position: absolute; top: 170px; left: 0; right: 0;
    font-size: 60px;
  }
  .web {
    position: absolute; bottom: 62px; left: 0; right: 0;
    text-align: center; font-size: 24px; font-weight: 600;
    color: var(--ink); letter-spacing: .06em;
  }
</style>
</head>
<body>
<main class="canvas">
  <section class="card card--front">
    <span class="brand-mark"></span>
    <h1 class="brand-name">Silver Harbor Rhythm</h1>
    <p class="person">Your Name, Title</p>
    <svg class="band" viewBox="0 0 820 470" aria-hidden="true">
      <path d="M0 300 Q410 230 820 268" fill="none" stroke="var(--green-line)" stroke-width="6"/>
      <path d="M0 318 Q410 250 820 282 L820 470 L0 470 Z" fill="var(--green-band)"/>
    </svg>
    <div class="contact">
      <div class="contact-row">Sreet Name, City Name, Zip Code-00000</div>
      <div class="contact-row">
        <svg viewBox="0 0 16 16"><circle cx="8" cy="8" r="8" fill="#fff"/><path d="M5 4l2 2-1 1c.6 1.3 1.7 2.4 3 3l1-1 2 2-1.2 1.2C7.5 12 4 8.5 3.8 5.2z" fill="var(--green-band)"/></svg>
        <span>555 274 9160</span>
      </div>
      <div class="contact-row contact-row--left">
        <svg viewBox="0 0 16 16"><rect x="1" y="3" width="14" height="10" rx="1.5" fill="#fff"/><path d="M1.5 4l6.5 5 6.5-5" fill="none" stroke="var(--green-band)" stroke-width="1.3"/></svg>
        <span>silverharborrhythm@mailnest.net</span>
        <span class="spacer"></span>
        <svg viewBox="0 0 16 16"><circle cx="8" cy="8" r="7" fill="#fff"/><path d="M1 8h14M8 1c-3 3.5-3 10.5 0 14M8 1c3 3.5 3 10.5 0 14" fill="none" stroke="var(--green-band)" stroke-width="1.1"/></svg>
        <span>www.silverharborrhythm.net</span>
      </div>
    </div>
  </section>

  <section class="card card--back">
    <h2 class="brand-name">Silver Harbor Rhythm</h2>
    <p class="web">www.silverharborrhythm.net</p>
  </section>
</main>
</body>
</html>
```